Business card design needed

I run a Beautician studio (for 7 years now)
I offer
- Velmo Body Sugaring
- Ruby Glaze
- Nails
- Facials
- Manicure
- Foot Treatment
It might not be necessary to list all those treatments?
Maybe the link to the Website is sufficient?
I leave that up to you ...
(more info on www.FernAndDewByLenka.com.au)
Velmo BodySugaring is our biggest success, It replaces waxing.
I would like to incorporate the logo into the Business Card.
We had many complaints regarding our old Business Cards as the Phone Number was to small.
On the backside, we would like a "your next Appointment" section.
Looking forward to you Design, cheers ... Lenka
Industry/Entity Type
Business
Contact Information for Business Card
Fern by Dew by Lenka
14 Korrin Sqr 3942 Berwick
www.FernAndDewByLenka.com.au
03 9481 2267

```html
<!DOCTYPE html>
<html lang="en">
<head>
<meta charset="utf-8">
<title>Velmo Body Sugaring – Business Cards</title>
<link href="https://fonts.googleapis.com/css2?family=Arimo:wght@400;700&family=Marcellus&family=Open+Sans:wght@400;600&display=swap" rel="stylesheet">
<style>
  :root {
    --backdrop: #2a2a2a;
    --card: #ffffff;
    --ink: #3a3a3a;
    --ink-soft: #555555;
    --green: #1e9b3c;
    --orange: #e8892a;
    --rule: #444444;
    --box: #666666;
    --faint: #eeeeee;
  }
  * { box-sizing: border-box; margin: 0; padding: 0; }
  html, body { width: 1200px; height: 728px; overflow: hidden; background: var(--backdrop); }
  .canvas { position: relative; width: 1200px; height: 728px; }
  .card { position: absolute; width: 541px; height: 308px; background: var(--card); overflow: hidden; font-family: "Arimo", sans-serif; color: var(--ink); }
  .card--front { left: 41px; top: 37px; }
  .card--appointment { left: 616px; top: 37px; }
  .card--hours { left: 43px; top: 380px; }
  .card--appointment-alt { left: 624px; top: 384px; }

  .brand { position: absolute; display: flex; align-items: center; gap: 10px; font-family: "Marcellus", serif; color: var(--ink); letter-spacing: 2px; text-transform: uppercase; }
  .brand__dot { width: 16px; height: 16px; border-radius: 50%; background: var(--orange); flex: none; }
  .card--front .brand { left: 26px; top: 95px; font-size: 22px; }
  .card--hours .brand { left: 0; right: 0; top: 110px; justify-content: center; font-size: 26px; }
  .brand--small { right: 40px; top: 60px; font-size: 11px; letter-spacing: 1px; gap: 6px; }
  .brand--small .brand__dot { width: 10px; height: 10px; }
  .brand--watermark { left: 0; right: 0; top: 195px; justify-content: center; font-size: 40px; color: var(--faint); }

  .treatments { position: absolute; left: 25px; top: 196px; }
  .treatments__title { font-size: 17px; font-weight: 700; color: var(--green); letter-spacing: 1px; margin-bottom: 3px; }
  .treatments__list { list-style: none; font-size: 14.5px; line-height: 21.5px; }
  .divider { position: absolute; left: 259px; top: 189px; width: 1.5px; height: 119px; background: var(--orange); }
  .contact { position: absolute; left: 278px; top: 196px; }
  .contact__name { font-size: 20px; font-weight: 700; color: var(--ink); }
  .contact__address { font-size: 14.5px; margin-top: 5px; }
  .contact__row { display: flex; align-items: center; gap: 8px; }
  .contact__phone { font-size: 17px; margin-top: 20px; }
  .contact__web { font-size: 14.5px; margin-top: 12px; }
  .icon { width: 15px; height: 15px; flex: none; }

  .appointment__title { position: absolute; left: 35px; top: 56px; font-family: "Marcellus", serif; font-size: 19px; color: var(--green); letter-spacing: 0.5px; }
  .form { position: absolute; left: 35px; top: 90px; font-family: "Open Sans", sans-serif; font-size: 15px; color: var(--ink); }
  .form__row { display: flex; align-items: flex-end; height: 38px; }
  .line { display: inline-block; border-bottom: 1px solid var(--ink-soft); margin: 0 6px 5px; }
  .line--dotted { border-bottom: 1px dotted var(--ink-soft); width: 300px; }
  .box { display: inline-block; width: 98px; height: 22px; border: 1px solid var(--box); margin-left: 10px; }
  .box + .box { margin-left: 26px; }
  .days { display: flex; align-items: center; gap: 6px; font-weight: 600; color: var(--ink-soft); font-size: 15px; margin-left: -4px; }
  .days__box { width: 34px; height: 20px; border: 1px solid var(--box); margin-right: 4px; }
  .note { position: absolute; left: 31px; top: 256px; width: 470px; font-family: "Open Sans", sans-serif; font-size: 13px; line-height: 17px; color: var(--ink); }

  .hours__web { position: absolute; left: 0; right: 0; top: 204px; text-align: center; font-family: "Open Sans", sans-serif; font-size: 14px; letter-spacing: 2.5px; color: var(--ink); }
  .hours__title { position: absolute; left: 0; right: 0; top: 236px; text-align: center; font-family: "Open Sans", sans-serif; font-size: 19px; font-weight: 600; letter-spacing: 1.5px; color: var(--ink-soft); }
  .hours__times { position: absolute; left: 0; right: 0; top: 270px; text-align: center; font-family: "Open Sans", sans-serif; font-size: 15px; font-weight: 600; color: var(--ink-soft); }
  .hours__sep { color: #aaaaaa; margin: 0 8px; font-weight: 400; }
</style>
</head>
<body>
<main class="canvas">

  <section class="card card--front">
    <div class="brand"><span class="brand__dot"></span>Velmo Body Sugaring</div>
    <div class="treatments">
      <h2 class="treatments__title">Treatments offer</h2>
      <ul class="treatments__list">
        <li>• Velmo Body Sugaring</li>
        <li>• Ruby Glaze • Nails</li>
        <li>• Facials • Manicure</li>
        <li>• Foot Treatment</li>
      </ul>
    </div>
    <div class="divider"></div>
    <div class="contact">
      <div class="contact__name">Fern by Dew by Lenka</div>
      <div class="contact__address">14 Korrin Sqr 3942 Berwick</div>
      <div class="contact__row contact__phone">
        <svg class="icon" viewBox="0 0 16 16" aria-hidden="true"><circle cx="8" cy="8" r="7" fill="none" stroke="var(--green)" stroke-width="1.4"/><path d="M5.5 4.5l1.5 0 .6 2-1 .8a5 5 0 0 0 2.1 2.1l.8-1 2 .6 0 1.5c-3.5.5-6.5-2.5-6-6z" fill="var(--green)"/></svg>
        03 9481 2267
      </div>
      <div class="contact__row contact__web">
        <svg class="icon" viewBox="0 0 16 16" aria-hidden="true"><g fill="none" stroke="var(--green)" stroke-width="1.2"><circle cx="8" cy="8" r="6.5"/><ellipse cx="8" cy="8" rx="2.8" ry="6.5"/><path d="M1.5 8h13M2.5 4.8h11M2.5 11.2h11"/></g></svg>
        www.FernAndDewByLenka.com.au
      </div>
    </div>
  </section>

  <section class="card card--appointment">
    <h2 class="appointment__title">YOUR APPOINTMENT</h2>
    <div class="brand brand--small"><span class="brand__dot"></span>Velmo Body Sugaring</div>
    <div class="form">
      <div class="form__row">Name :<span class="line line--dotted"></span></div>
      <div class="form__row">Date :<span class="line" style="width:96px;margin-left:20px"></span>Time :<span class="line" style="width:90px;margin-right:2px"></span>am / pm</div>
      <div class="form__row" style="align-items:center">Next Appointment<span class="box"></span><span class="box"></span></div>
      <div class="form__row days">MON<span class="days__box"></span>TUE<span class="days__box"></span>WED<span class="days__box"></span>THU<span class="days__box"></span>FRI<span class="days__box"></span>SAT<span class="days__box"></span></div>
    </div>
    <p class="note">It would be appreciated if 24 hours notice could be given if you are unable to attend an appointment</p>
  </section>

  <section class="card card--hours">
    <div class="brand"><span class="brand__dot"></span>Velmo Body Sugaring</div>
    <div class="hours__web">www.FernAndDewByLenka.com.au</div>
    <h2 class="hours__title">Hours of Operation</h2>
    <div class="hours__times">Mon - Fri: 7.30am - 7.00pm<span class="hours__sep">|</span>Saturday: 7.30am - 12.00pm</div>
  </section>

  <section class="card card--appointment-alt">
    <div class="brand brand--watermark">Velmo Body Sugaring</div>
    <h2 class="appointment__title">YOUR APPOINTMENT</h2>
    <div class="form">
      <div class="form__row">Name :<span class="line line--dotted"></span></div>
      <div class="form__row">Date :<span class="line" style="width:96px;margin-left:20px"></span>Time :<span class="line" style="width:90px;margin-right:2px"></span>am / pm</div>
      <div class="form__row" style="align-items:center">Next Appointment<span class="box"></span><span class="box"></span></div>
      <div class="form__row days">MON<span class="days__box"></span>TUE<span class="days__box"></span>WED<span class="days__box"></span>THU<span class="days__box"></span>FRI<span class="days__box"></span>SAT<span class="days__box"></span></div>
    </div>
    <p class="note">It would be appreciated if 24 hours notice could be given if you are unable to attend an appointment</p>
  </section>

</main>
</body>
</html>
```